Packaged Food Business Needs a Packaging Design

We need a package design to be used as a label/sticker on the lids of round and square transparent plastic containers and on the sides of resealable stand-up pouches. The brand name is 'Savorine' - please find attached logo together with pictures of the sample containers and pouch. We will use the packaging to market a wide variety of food categories from nuts, dried fruits, spices, cooking chocolates, baking ingredients, cereals, grains and pulses.

OVERALL FEEDBACK ON DESIGNS ALREADY RECEIVED:

- We have found so far that a lot of our mandatory requirements are not adhered to in designs that have been submitted so far. We would like to emphasise that the ingredient, weight and expiry text will be printed at the time of packing so it should not take prime space on the pack BUT at the same time some 'blank' space needs to flawlessly be incorporated into the overall design for this purpose
- We encourage you to glorify the brand logo in the pack, and absolutely refrain from duplicating the tagline
- Please note that ONE label design will be used to pack a wide variety of food ingredients and therefore please ensure that the choice of your design incorporates this requirement, in the past we have received designs that are limited to only one type of food (like nuts) or have received designs that are too floral or leafy (and not grounded to food
- Please ensure that you submit designs for all three packaging formats, it is critical to see the family look from the on-set

Target Market(s)

The brand is targeting both mothers and professional chefs and therefore the label design should be broadly approachable and convey affordable premium

Industry/Entity Type

Business

Requirements
Must have
• - Consistent with the brand name and logo, the overall look and feel of the packaging should convey values of healthy, gourmet food ingredients, high in nourishment and project a sense of delightful taste
• - The design styling to be modern and 'simplistic' (embracing 'less-is-more' type of a design style)
• - Design a packaging architecture that incorporates the brand logo together with its tagline lock-up of 'taste the goodness in every spoonful' - find logo attached
• - The design needs to have a dedicated area to print the ingredient (e.g., Mixed Nuts), weight (e.g., 500g) and expiry (this space needs to be flawlessly incorporated into the design) - this information will be printed either with an inkjet printer or with a rubber stamp so please leave an empty space (the text should not be part of the design, just the area for the text needs to be included in the design)
• - The packaging must include 'Packed By: Kestomar Traders Ltd, P. O. Box 51946, Kampala - Uganda'
• - For the design of the resealable pouch, please incorporate a window to see through the ingredients and a hole on top to hang on supermarket pegs if necessary
Nice to have
• - We would love to have some design submissions that are bold and cheerful and fun (but not frivolous) - please see attached inspiration for 'fun' packaging. The attachments are purely for inspiration, not to infringe on anyone else's TM and copyrights
• - Incorporate green to convey healthy, organic values
• - Explore use of gold and silver convey premiumness
Should not have
• - Do not duplicate the tagline
• - Do not include the ingredient, weight and expiry in the main graphic of the design, these will be printed at the time of packing so ensure there is provision for this in a flawless way in the design (e.g., via a blank space allocated for this purpose)

```html
<!DOCTYPE html>
<html lang="en">
<head>
<meta charset="utf-8">
<title>Savorine – Packaging Label Family</title>
<link rel="stylesheet" href="https://fonts.googleapis.com/css2?family=Oswald:wght@300;600&family=Montserrat:wght@700&display=swap">
<style>
  :root {
    --orange: #e44d2a;
    --gold: #f2a41c;
    --indigo: #3f3a93;
    --brown: #3d1f0e;
    --green: #5a9a2e;
    --leaf: #8cc63f;
    --white: #ffffff;
    --window: #5f5f5f;
    --outline: #222222;
  }
  * { box-sizing: border-box; margin: 0; padding: 0; }
  html, body { width: 1200px; height: 1200px; overflow: hidden; background: var(--white); }
  .canvas { position: relative; width: 1200px; height: 1200px; background: var(--white); }

  .pattern {
    position: absolute;
    background:
      radial-gradient(circle at 20% 30%, var(--orange) 0 14%, transparent 15%),
      radial-gradient(circle at 70% 60%, var(--orange) 0 12%, transparent 13%),
      radial-gradient(circle at 45% 80%, var(--gold) 0 9%, transparent 10%),
      linear-gradient(135deg, #fbe3d6, #f7c7a8 45%, #fde9c7 70%, #e9e6f5);
  }
  .band { position: absolute; left: 0; right: 0; background: var(--orange); }
  .band-credit {
    display: flex; align-items: center; justify-content: center;
    font-family: "Oswald", sans-serif; font-weight: 300;
    color: var(--white); text-transform: uppercase; white-space: nowrap;
  }

  .lockup { position: absolute; left: 0; right: 0; display: flex; flex-direction: column; align-items: center; }
  .brand-dot { border-radius: 50%; background: var(--green); }
  .brand-name {
    font-family: "Oswald", sans-serif; font-weight: 600;
    color: var(--brown); text-transform: uppercase; line-height: 1;
  }
  .tagline {
    font-family: "Montserrat", sans-serif; font-weight: 700;
    color: var(--green); text-transform: uppercase; white-space: nowrap;
  }

  /* Pouch */
  .pouch { position: absolute; left: 44px; top: 148px; width: 575px; height: 862px; border: 1px solid var(--outline); background: var(--white); overflow: hidden; }
  .pouch .pattern { left: 16px; top: 16px; width: 541px; height: 554px; }
  .pouch .hang-hole { position: absolute; left: 217px; top: 23px; }
  .pouch .window { position: absolute; left: 77px; top: 98px; width: 423px; height: 454px; border-radius: 21px; background: var(--window); }
  .pouch .band-credit { top: 586px; height: 18px; font-size: 11.5px; }
  .pouch .band-foot { top: 812px; height: 50px; }
  .pouch .lockup { top: 622px; }
  .pouch .brand-dot { width: 46px; height: 46px; margin-bottom: 10px; }
  .pouch .brand-name { font-size: 84px; letter-spacing: 0.1em; }
  .pouch .tagline { font-size: 15px; letter-spacing: 0.16em; margin-top: 14px; }

  /* Round lid */
  .round-lid { position: absolute; left: 708px; top: 181px; width: 398px; height: 398px; border-radius: 50%; border: 1px solid var(--outline); overflow: hidden; background: var(--white); }
  .round-lid .pattern-top { left: 0; top: 0; width: 100%; height: 114px; }
  .round-lid .pattern-bottom { left: 0; top: 306px; width: 100%; height: 92px; }
  .round-lid .band-credit { top: 113px; height: 16px; font-size: 10.5px; }
  .round-lid .band-foot { top: 269px; height: 37px; }
  .round-lid .lockup { top: 134px; }
  .round-lid .brand-dot { width: 30px; height: 30px; margin-bottom: 8px; }
  .round-lid .brand-name { font-size: 56px; letter-spacing: 0.1em; }
  .round-lid .tagline { font-size: 10px; letter-spacing: 0.14em; margin-top: 8px; }

  /* Square lid */
  .square-lid { position: absolute; left: 669px; top: 627px; width: 468px; height: 301px; border: 1px solid var(--outline); overflow: hidden; background: var(--white); }
  .square-lid .pattern-top { left: 8px; top: 6px; width: 452px; height: 50px; }
  .square-lid .pattern-bottom { left: 8px; top: 245px; width: 452px; height: 48px; }
  .square-lid .band-credit { top: 56px; height: 15px; font-size: 10.5px; }
  .square-lid .band-foot { top: 213px; height: 32px; }
  .square-lid .lockup { top: 76px; }
  .square-lid .brand-dot { width: 28px; height: 28px; margin-bottom: 7px; }
  .square-lid .brand-name { font-size: 58px; letter-spacing: 0.1em; }
  .square-lid .tagline { font-size: 10px; letter-spacing: 0.15em; margin-top: 8px; }
</style>
</head>
<body>
<main class="canvas">

  <section class="pouch" aria-label="Stand-up pouch label">
    <div class="pattern" role="img" aria-label="Decorative paisley pattern in orange, gold and indigo"></div>
    <svg class="hang-hole" width="143" height="56" viewBox="0 0 143 56" aria-hidden="true">
      <path d="M14 18 H60 Q62 4 71 2 Q80 4 82 18 H129 Q141 18 141 34 Q141 50 129 50 H14 Q2 50 2 34 Q2 18 14 18 Z" fill="var(--window)"/>
    </svg>
    <div class="window" aria-label="Clear window"></div>
    <div class="band band-credit">Packed by Kestomar Traders Ltd, P. O. Box 51946, Kampala - Uganda</div>
    <div class="lockup">
      <span class="brand-dot" aria-hidden="true"></span>
      <span class="brand-name">Savorine</span>
      <span class="tagline">Taste the goodness in every spoonful!</span>
    </div>
    <div class="band band-foot" aria-label="Print area for ingredient, weight and expiry"></div>
  </section>

  <section class="round-lid" aria-label="Round lid label">
    <div class="pattern pattern-top" role="img" aria-label="Decorative paisley pattern in orange, gold and indigo"></div>
    <div class="band band-credit">Packed by Kestomar Traders Ltd, P. O. Box 51946, Kampala - Uganda</div>
    <div class="lockup">
      <span class="brand-dot" aria-hidden="true"></span>
      <span class="brand-name">Savorine</span>
      <span class="tagline">Taste the goodness in every spoonful!</span>
    </div>
    <div class="band band-foot" aria-label="Print area for ingredient, weight and expiry"></div>
    <div class="pattern pattern-bottom" role="img" aria-label="Decorative paisley pattern in orange, gold and indigo"></div>
  </section>

  <section class="square-lid" aria-label="Square lid label">
    <div class="pattern pattern-top" role="img" aria-label="Decorative paisley pattern in orange, gold and indigo"></div>
    <div class="band band-credit">Packed by Kestomar Traders Ltd, P. O. Box 51946, Kampala - Uganda</div>
    <div class="lockup">
      <span class="brand-dot" aria-hidden="true"></span>
      <span class="brand-name">Savorine</span>
      <span class="tagline">Taste the goodness in every spoonful!</span>
    </div>
    <div class="band band-foot" aria-label="Print area for ingredient, weight and expiry"></div>
    <div class="pattern pattern-bottom" role="img" aria-label="Decorative paisley pattern in orange, gold and indigo"></div>
  </section>

</main>
</body>
</html>
```